Colin Vardek Business card

Hey there, I’m hoping to have a business card designed. I’m in Real estate and just switched to a new Brokerage called: The Harbourline Property Group

The back could just be the company name maybe or whatever looks good!

I’ve attached some logos of our company and some cards my buddy had done up.

On the card:
Colin Vardek
colinvardek@mailora.com
587-412-9065
colinvardek.ca

Target Market(s)

Home buyers and sellers

Industry/Entity Type

Real Estate

Contact Information for Business Card

just looking for a cool and modern design with my picture on it. I like the idea of Black and red being used.

Requirements
Must have
• all the details provided. I'm open to anything. Just want a professional looking card.

```html
<!DOCTYPE html>
<html lang="en">
<head>
<meta charset="utf-8">
<title>Colin Vardek – Business Card</title>
<link href="https://fonts.googleapis.com/css2?family=Montserrat:wght@800&family=Roboto:wght@400;500&display=swap" rel="stylesheet">
<style>
  :root{
    --stage:#2a2a2b;
    --card:#2f2f31;
    --card-light:#3b3b3d;
    --red:#d42a3f;
    --white:#ffffff;
    --ink:#1d1d1f;
    --text:#e6e6e6;
    --photo-a:#4a4a4c;
    --photo-b:#2b2b2e;
  }
  *{margin:0;padding:0;box-sizing:border-box}
  html,body{width:1200px;height:852px;overflow:hidden;background:var(--stage)}
  .stage{position:relative;width:1200px;height:852px}
  .card{
    position:absolute;width:560px;height:320px;border-radius:22px;
    background:var(--card);overflow:hidden;
    box-shadow:0 5px 0 var(--red);
  }
  .card--back{left:70px;top:70px;display:flex;align-items:center;justify-content:center}
  .card--front{left:570px;top:450px}
  .brand{
    font-family:'Montserrat',sans-serif;font-weight:800;text-transform:uppercase;
    line-height:1.05;letter-spacing:.5px;
  }
  .card--back .brand{color:var(--ink);font-size:34px;text-align:center;width:380px}
  .front-panel{position:absolute;right:0;top:0;width:330px;height:100%;background:var(--card-light);
    clip-path:polygon(18% 0,100% 0,100% 100%,0 100%)}
  .portrait{position:absolute;right:0;top:0;width:250px;height:100%;
    background:linear-gradient(160deg,var(--photo-a),var(--photo-b))}
  .front-brand{position:absolute;left:34px;top:62px;display:flex;align-items:flex-start;gap:10px}
  .front-brand .mark{width:12px;height:12px;background:var(--red);margin-top:6px;flex:none}
  .front-brand .brand{color:var(--white);font-size:24px;width:230px}
  .agent-name{position:absolute;left:58px;top:182px;font-family:'Roboto',sans-serif;font-weight:500;
    font-size:22px;color:var(--red)}
  .accent-bar{position:absolute;left:0;top:212px;width:14px;height:34px;background:var(--red)}
  .contact{position:absolute;left:58px;top:222px;list-style:none;font-family:'Roboto',sans-serif;
    font-size:15px;color:var(--text)}
  .contact li{display:flex;align-items:center;gap:9px;height:24px}
  .contact svg{width:13px;height:13px;fill:var(--red);flex:none}
</style>
</head>
<body>
<div class="stage">
  <section class="card card--back">
    <div class="brand">The Harbourline Property Group</div>
  </section>

  <section class="card card--front">
    <div class="front-panel"></div>
    <div class="portrait" role="img" aria-label="Portrait photo of Colin Vardek in a dark blazer and white shirt"></div>
    <div class="front-brand">
      <span class="mark"></span>
      <div class="brand">The Harbourline Property Group</div>
    </div>
    <div class="agent-name">Colin Vardek</div>
    <span class="accent-bar"></span>
    <ul class="contact">
      <li><svg viewBox="0 0 24 24"><path d="M6.6 10.8a15 15 0 0 0 6.6 6.6l2.2-2.2c.3-.3.7-.4 1-.2 1.1.4 2.3.6 3.6.6.6 0 1 .4 1 1V20c0 .6-.4 1-1 1A17 17 0 0 1 3 4c0-.6.4-1 1-1h3.5c.6 0 1 .4 1 1 0 1.3.2 2.5.6 3.6.1.3 0 .7-.2 1z"/></svg>587-412-9065</li>
      <li><svg viewBox="0 0 24 24"><path d="M2 5h20v14H2zm2 2v.5l8 5 8-5V7l-8 5z"/></svg>colinvardek@mailora.com</li>
      <li><svg viewBox="0 0 24 24"><circle cx="12" cy="12" r="10"/></svg>colinvardek.ca</li>
    </ul>
  </section>
</div>
</body>
</html>
```